Flaschenetiketten-Design in rechteckiger Grundform für Biermanufaktur
Zielgruppe
Wir repräsentieren eine Bier-Manufaktur in der Gründungsphase und sind auf der Suche nach einem Designvorschlag für die Flaschenetiketten.
Unsere Zielgruppe sind Liebhaber, die auf der Suche nach dem Speziellen und Lokalen sind. Der Biergenuss abseits des Massenmarktes soll im Entwurf sichtbar/transportiert werden. Die Bier-Manufaktur steht zeitgleich für Trend-Kreationen mit bodenständigem Ursprung.
Aufgabenstellung
Die Herkunft der Gründer Familie aus dem Schweizer Kanton Simplon soll im Vordergrund stehen, hierzu bitte das Familienwappen / einzelne Elemente siehe Dateiupload berücksichtigen.
Das Etikett soll eine rechteckige Grundform haben.
Folgende Angaben sollen sich im Etikett wiederfinden:
- Biersorte: 'Lager' (zukünftig soll es möglich sein, Biersorte auf dem Etikett zu wechseln)
Brand: 'Hearty Kandrom'
'Biermanufaktur Walliser Ursprungs'
Die Schrift soll klar und nicht zu verspielt sein.

```html
<!DOCTYPE html>
<html lang="de">
<head>
<meta charset="utf-8">
<title>Hearty Kandrom – Etikettenserie</title>
<link rel="stylesheet" href="https://fonts.googleapis.com/css2?family=Oswald:wght@400;600&display=swap">
<style>
  :root {
    --bg: #ececec;
    --white: #f7f7f5;
    --royal: #1d4a94;
    --royal-deep: #143a7a;
    --sky: #3a8fd6;
    --sky-light: #4aa3e4;
    --black: #1b1b1d;
    --gold: #c9a13a;
    --gold-light: #e6c766;
    --red: #b3202b;
    --grey-faint: #d9d9d9;
    --ink-dark: #5a1a12;
  }
  * { box-sizing: border-box; margin: 0; padding: 0; }
  html, body { width: 1200px; height: 803px; overflow: hidden; background: var(--bg); }
  body { font-family: "Oswald", "Arial Narrow", sans-serif; position: relative; }

  .label-set { position: absolute; top: 0; width: 240px; height: 803px; }
  .set-1 { left: 45px; } .set-2 { left: 335px; } .set-3 { left: 625px; } .set-4 { left: 915px; }

  .neck-label {
    position: absolute; top: 80px; left: 55px; width: 130px; height: 140px;
    display: flex; align-items: center; justify-content: center;
  }
  .body-label {
    position: absolute; top: 270px; left: 0; width: 240px; height: 400px;
    overflow: hidden; text-align: center;
  }

  .crest {
    width: 58px; height: 72px; border-radius: 4px 4px 26px 26px;
    background: linear-gradient(180deg, var(--royal) 0%, var(--royal) 70%, #2d6b3a 100%);
    border: 3px solid var(--gold);
  }
  .crest-wreath {
    width: 96px; height: 100px; border-radius: 50%;
    display: flex; align-items: center; justify-content: center;
  }

  /* Set 1 */
  .set-1 .neck-label { background: var(--white); }
  .set-1 .neck-label::before, .set-1 .neck-label::after {
    content: ""; position: absolute; left: 0; right: 0; height: 8px; background: var(--gold);
  }
  .set-1 .neck-label::before { top: 50px; } .set-1 .neck-label::after { top: 80px; }
  .set-1 .neck-label .crest { position: relative; z-index: 1; }
  .set-1 .body-label { background: var(--white); border-top: 5px solid var(--gold); border-bottom: 5px solid var(--gold); }
  .set-1 .frame {
    position: absolute; left: 14px; top: 30px; width: 212px; height: 280px; border-radius: 40%;
    background: radial-gradient(circle, var(--gold-light) 0%, var(--gold) 70%, #8a6a1f 100%);
  }
  .set-1 .oval {
    position: absolute; left: 32px; top: 100px; width: 176px; height: 190px; border-radius: 50%;
    background: var(--royal); border: 4px solid var(--white);
    display: flex; flex-direction: column; align-items: center; justify-content: center;
  }
  .set-1 .frame-crest { position: absolute; left: 91px; top: 40px; z-index: 2; }
  .set-1 .name { color: var(--white); font-weight: 600; font-size: 40px; line-height: 0.98; letter-spacing: 0; }
  .set-1 .maker { color: var(--white); font-size: 12px; line-height: 1.2; margin-top: 8px; }
  .set-1 .hops { position: absolute; left: 30px; right: 30px; bottom: 12px; height: 50px; border-radius: 25px; background: linear-gradient(90deg, transparent, var(--grey-faint), transparent); }

  /* Shared layout for sets 2–4 */
  .quality { position: absolute; left: 0; right: 0; top: 22px; font-size: 8px; letter-spacing: 1px; }
  .crest-area { position: absolute; left: 72px; top: 40px; width: 96px; height: 100px; }
  .name-block { position: absolute; left: 0; right: 0; top: 160px; font-weight: 600; font-size: 48px; line-height: 0.98; }
  .maker-band { position: absolute; left: 0; right: 0; bottom: 0; height: 88px; padding-top: 18px; font-size: 15px; line-height: 1.45; color: var(--white); }

  /* Set 2 */
  .set-2 .neck-label { background: var(--royal); border-top: 6px solid var(--gold); border-bottom: 6px solid var(--gold); }
  .set-2 .crest-wreath, .set-3 .crest-wreath { background: radial-gradient(circle, transparent 40%, rgba(74,163,228,0.55) 41%, transparent 72%); }
  .set-2 .body-label { background: linear-gradient(180deg, var(--royal-deep), var(--royal)); border-top: 4px solid var(--gold); border-bottom: 4px solid var(--gold); }
  .set-2 .quality { color: var(--white); }
  .set-2 .name-block { color: var(--white); }
  .set-2 .maker-band { background: linear-gradient(180deg, var(--sky), var(--sky-light)); }

  /* Set 3 */
  .set-3 .neck-label { background: var(--black); border-top: 5px solid var(--sky); border-bottom: 5px solid var(--sky); }
  .set-3 .body-label { background: var(--black); border-top: 4px solid var(--sky); }
  .set-3 .crest-wreath { background: radial-gradient(circle, transparent 40%, rgba(200,200,200,0.45) 41%, transparent 72%); }
  .set-3 .quality { color: #dcdcdc; }
  .set-3 .name-block { color: #e8e8e8; }
  .set-3 .maker-band { background: linear-gradient(180deg, #2f7cc4, var(--sky-light)); }

  /* Set 4 */
  .set-4 .neck-label { background: var(--white); border-top: 4px solid var(--gold); border-bottom: 4px solid var(--gold); }
  .set-4 .crest-wreath { background: radial-gradient(circle, transparent 40%, rgba(201,161,58,0.6) 41%, transparent 72%); }
  .set-4 .body-label { background: var(--white); }
  .set-4 .quality { color: #333; }
  .set-4 .name-block { color: var(--red); top: 165px; }
  .set-4 .side-hops { position: absolute; top: 50px; width: 34px; height: 90px; border-radius: 17px; background: var(--grey-faint); }
  .set-4 .side-hops.left { left: 16px; } .set-4 .side-hops.right { right: 16px; }
  .set-4 .maker-band {
    bottom: 34px; left: -20px; right: -20px; height: 70px; padding-top: 10px;
    background: linear-gradient(90deg, #b88f2c, var(--gold-light));
    color: var(--ink-dark); transform: rotate(-8deg);
  }
</style>
</head>
<body>
  <section class="label-set set-1">
    <div class="neck-label"><div class="crest" role="img" aria-label="Familienwappen"></div></div>
    <div class="body-label">
      <div class="frame" role="img" aria-label="Goldener barocker Zierrahmen"></div>
      <div class="crest frame-crest" role="img" aria-label="Familienwappen"></div>
      <div class="oval">
        <div class="name">HEARTY<br>KANDROM</div>
        <div class="maker">Biermanufaktur Walliser<br>Ursprungs</div>
      </div>
      <div class="hops" role="img" aria-label="Dezentes Hopfenornament"></div>
    </div>
  </section>

  <section class="label-set set-2">
    <div class="neck-label"><div class="crest-wreath" role="img" aria-label="Wappen mit Ährenkranz"><div class="crest"></div></div></div>
    <div class="body-label">
      <div class="quality">PREMIUM QUALITÄT</div>
      <div class="crest-area crest-wreath" role="img" aria-label="Wappen mit Ährenkranz"><div class="crest"></div></div>
      <div class="name-block">HEARTY<br>KANDROM</div>
      <div class="maker-band">Biermanufaktur Walliser<br>Ursprungs</div>
    </div>
  </section>

  <section class="label-set set-3">
    <div class="neck-label"><div class="crest-wreath" role="img" aria-label="Wappen mit Ährenkranz"><div class="crest"></div></div></div>
    <div class="body-label">
      <div class="quality">PREMIUM QUALITÄT</div>
      <div class="crest-area crest-wreath" role="img" aria-label="Wappen mit Ährenkranz"><div class="crest"></div></div>
      <div class="name-block">Hearty<br>Kandrom</div>
      <div class="maker-band">Biermanufaktur Walliser<br>Ursprungs</div>
    </div>
  </section>

  <section class="label-set set-4">
    <div class="neck-label"><div class="crest-wreath" role="img" aria-label="Wappen mit goldenem Ährenkranz"><div class="crest"></div></div></div>
    <div class="body-label">
      <div class="side-hops left" role="img" aria-label="Hopfenornament"></div>
      <div class="side-hops right" role="img" aria-label="Hopfenornament"></div>
      <div class="quality">PREMIUM QUALITÄT</div>
      <div class="crest-area crest-wreath" role="img" aria-label="Wappen mit goldenem Ährenkranz"><div class="crest"></div></div>
      <div class="name-block">HEARTY<br>KANDROM</div>
      <div class="maker-band">Biermanufaktur Walliser<br>Ursprungs</div>
    </div>
  </section>
</body>
</html>
```